Advertising company unique advertising platform

we need a logo design for a new company based in Australia Melbourne. We develop innovated advertising platform where consumer can use this platform to get regular discount, as business owner they can use this platform for free advertisement. Payment for this advertisement platform only payable every two weeks, when I generate revenue for their business

Industry/Entity Type

Advertising

Contact Information for Business Card

Dale Morven | Co-Founder |Managing Director
Suite 718 240 Wattlebrook Lane Melbourne Vic 3000

ABN 38 614 207 923
Tel: +61 0487 259 318 | Email: dale.morven@plivorantu.com

Font styles to use
Decorative
Script

Requirements
Must have
• Try few different design and some round corner business card
Should not have
• One round corner business card...try 4 different colour background not only black, make sure two side is designed. Be creative so imagine you are giving this to a client make sure has wow factor, if you can also try one design with engrave like all the logo, words look 3d feel
• The word Advertising Platform use attached file font

```html
<!DOCTYPE html>
<html lang="en">
<head>
<meta charset="utf-8">
<title>Vantory Loop Business Card</title>
<link href="https://fonts.googleapis.com/css2?family=Roboto:wght@400;500;700&display=swap" rel="stylesheet">
<style>
  :root {
    --bg: #e9e7e4;
    --card-dark: #2b2b2d;
    --ink-dark: #232326;
    --mint: #18ecaa;
    --lavender: #8aa3e2;
    --sky: #0bc3f0;
    --flame: #f2512f;
    --amber: #f7b733;
    --teal-text: #22e3b6;
    --white: #f4f4f4;
    --rule: #d8d8d8;
  }
  * { box-sizing: border-box; margin: 0; padding: 0; }
  html, body { width: 1200px; height: 886px; overflow: hidden; }
  body {
    background: var(--bg);
    font-family: "Roboto", Arial, sans-serif;
    position: relative;
  }
  .card {
    position: absolute;
    width: 560px;
    height: 340px;
    border-radius: 22px;
    overflow: hidden;
    box-shadow: 0 10px 28px rgba(0,0,0,0.18);
  }
  /* Front */
  .card-front {
    left: 50px; top: 70px;
    background: linear-gradient(110deg, var(--mint) 0%, var(--lavender) 50%, var(--sky) 100%);
  }
  .front-brand {
    position: absolute;
    left: 0; right: 0; top: 118px;
    display: flex; align-items: center; justify-content: center; gap: 14px;
  }
  .brand-dot {
    width: 54px; height: 54px; border-radius: 50%;
    background: var(--ink-dark);
  }
  .brand-name {
    font-weight: 700; font-size: 40px; color: var(--ink-dark);
    letter-spacing: 0.5px;
  }
  .front-web {
    position: absolute; left: 0; right: 0; top: 262px;
    text-align: center; font-size: 14px; letter-spacing: 5px;
    color: var(--ink-dark);
  }
  /* Back */
  .card-back {
    left: 590px; top: 476px;
    background: var(--card-dark);
    color: var(--white);
  }
  .person { position: absolute; left: 34px; top: 40px; }
  .person-name {
    font-weight: 700; font-size: 22px; color: var(--flame); text-transform: uppercase;
  }
  .person-role {
    font-weight: 500; font-size: 15px; color: var(--teal-text); text-transform: uppercase; line-height: 1.25; margin-top: 4px;
  }
  .rule-short {
    position: absolute; left: 34px; top: 120px; width: 500px; height: 1px; background: var(--rule);
  }
  .contact { position: absolute; left: 34px; top: 132px; font-size: 15px; line-height: 1.45; }
  .contact-row { display: flex; align-items: center; gap: 8px; }
  .contact-row svg { width: 14px; height: 14px; flex: none; }
  .contact-plain { padding-left: 0; }
  .back-brand {
    position: absolute; right: 34px; top: 44px;
    display: flex; align-items: center; gap: 10px;
  }
  .back-brand .brand-dot { width: 40px; height: 40px; background: var(--flame); }
  .back-brand .brand-name { font-size: 28px; color: var(--flame); }
  .rule-long {
    position: absolute; left: 34px; right: 34px; top: 226px; height: 1px; background: var(--rule);
  }
  .address {
    position: absolute; right: 34px; top: 238px; text-align: right; font-size: 15px; line-height: 1.4;
  }
  .strip-left {
    position: absolute; left: 0; bottom: 0; width: 330px; height: 8px;
    background: linear-gradient(90deg, var(--mint), var(--lavender), var(--sky));
  }
  .web-tab {
    position: absolute; right: 0; bottom: 0; width: 240px; height: 34px;
    background: linear-gradient(90deg, var(--flame), var(--amber) 60%, var(--flame));
    clip-path: polygon(28px 0, 100% 0, 100% 100%, 0 100%);
    display: flex; align-items: center; justify-content: flex-end; padding-right: 22px;
    font-size: 15px; letter-spacing: 2px; color: var(--white);
  }
</style>
</head>
<body>
  <section class="card card-front">
    <div class="front-brand">
      <span class="brand-dot"></span>
      <span class="brand-name">Vantory Loop</span>
    </div>
    <p class="front-web">www.plivorantu.com</p>
  </section>

  <section class="card card-back">
    <div class="person">
      <p class="person-name">Dale Morven</p>
      <p class="person-role">Co-Founder<br>Managing Director</p>
    </div>
    <div class="back-brand">
      <span class="brand-dot"></span>
      <span class="brand-name">Vantory Loop</span>
    </div>
    <div class="rule-short"></div>
    <div class="contact">
      <p class="contact-row">
        <svg viewBox="0 0 24 24" aria-hidden="true"><path fill="#f2512f" d="M6.6 10.8a15.1 15.1 0 0 0 6.6 6.6l2.2-2.2a1 1 0 0 1 1-.25 11.4 11.4 0 0 0 3.6.57 1 1 0 0 1 1 1V20a1 1 0 0 1-1 1A17 17 0 0 1 3 4a1 1 0 0 1 1-1h3.5a1 1 0 0 1 1 1c0 1.25.2 2.45.57 3.57a1 1 0 0 1-.25 1z"/></svg>
        +61 0487 259 318
      </p>
      <p class="contact-row">
        <svg viewBox="0 0 24 24" aria-hidden="true"><path fill="#f2512f" d="M2 5h20v14H2z"/><path fill="none" stroke="#2b2b2d" stroke-width="2" d="M2 5l10 8 10-8"/></svg>
        dale.morven@plivorantu.com
      </p>
      <p class="contact-plain">Plivorantu</p>
      <p class="contact-plain">ABN 38 614 207 923</p>
    </div>
    <div class="rule-long"></div>
    <div class="address">
      <p>Suite 718 240 Wattlebrook Lane</p>
      <p>Melbourne Vic 3000</p>
    </div>
    <div class="strip-left"></div>
    <div class="web-tab">www.plivorantu.com</div>
  </section>
</body>
</html>
```